Marlowe Group needs a business card

I would like the card to be simple but modern and elegant.
I like black and white.
or black and gold.
we are a private finance lender and also are involved in property and property developments.

please look at the business card photos i provided i would like M.G only one one side and all the other details on the other side use fonts that tie in with my theme.

Industry/Entity Type

Finance

Contact Information for Business Card

Marlowe Group (M.G) Daniel Marlowe M: 0413586207 E: danmarl@inboxmail.test

Font styles to use
Other font styles liked:
• Use fonts that would reflect our business

Colors
000000
ffffff

Requirements
Must have
• one side of details
• other side has either M.G or Marlowe Group like in the photos provided

```html
<!DOCTYPE html>
<html lang="en">
<head>
<meta charset="utf-8">
<title>Marlowe Group — Business Card</title>
<link rel="stylesheet" href="https://fonts.googleapis.com/css2?family=Montserrat:wght@500;700&display=swap">
<style>
  :root {
    --backdrop: #7f8283;
    --card-black: #111111;
    --card-white: #f7f7f7;
    --ink-white: #ffffff;
    --ink-black: #000000;
    --card-shadow: rgba(0, 0, 0, 0.28);
  }
  html, body {
    margin: 0;
    padding: 0;
    width: 1200px;
    height: 814px;
    overflow: hidden;
    background: var(--backdrop);
  }
  .canvas {
    width: 1200px;
    height: 814px;
    display: flex;
    align-items: center;
    justify-content: center;
    gap: 56px;
  }
  .card {
    width: 520px;
    height: 297px;
    border-radius: 3px;
    box-shadow: 0 10px 26px var(--card-shadow);
    display: flex;
    flex-direction: column;
    align-items: center;
    justify-content: center;
    box-sizing: border-box;
  }
  .card--details {
    background: var(--card-black);
    color: var(--ink-white);
    font-family: "Montserrat", Arial, sans-serif;
    font-weight: 500;
    text-align: center;
  }
  .card__name {
    margin: 0 0 10px;
    font-size: 21px;
    font-weight: 500;
    letter-spacing: 0.3px;
  }
  .card__contact {
    margin: 0;
    padding: 0;
    list-style: none;
    font-size: 15.5px;
    line-height: 1.5;
    letter-spacing: 0.4px;
  }
  .card--monogram {
    background: var(--card-white);
  }
  .card__monogram {
    margin: 0;
    font-family: "Montserrat", Arial, sans-serif;
    font-weight: 700;
    font-size: 64px;
    letter-spacing: 2px;
    color: var(--ink-black);
  }
</style>
</head>
<body>
  <main class="canvas">
    <section class="card card--details" aria-label="Card back with contact details">
      <h1 class="card__name">Daniel Marlowe</h1>
      <ul class="card__contact">
        <li>Cell : 0413586207</li>
        <li>danmarl@inboxmail.test</li>
        <li>www.marlowegroup.test</li>
      </ul>
    </section>
    <section class="card card--monogram" aria-label="Card front with monogram">
      <p class="card__monogram">M.G</p>
    </section>
  </main>
</body>
</html>
```